Wandering Rooms Stationary Set

Wandering Rooms is a bespoke interior design firm set to provide services to VIP clients with elegance and minimalism is the main theme for our stationary set. We require a full stationary set covering A4 letterhead, A4 & A3 envelopes, business cards, USB's, CDs, email signature and any other item the designer sees fit. logo is already designed and finalized, and we require the designer to use it as is without modifying the logo.

Address to be used on letterhead / business cards ...etc shall be as follows:

Phone : +971 2 518 2047
P.O. Box : 309186
Address: Block C&D, Bldg. 47, Court 12, Abu Dhabi, United Arab Emirates
Website: www.wanderingrooms-example.com

Target Market(s)

VIP Clients

Industry/Entity Type

Interior Design

Font styles to use
Other font styles liked:
• something to be unique

Colors

Designer to choose colors to be used in the design.

Requirements
Must have
• Elegant, minimalistic
Nice to have
• Simple yet elegant design having a sharp yet clean cut format
Should not have
• No additional colours, just colours that are used in the logo (silver, black or gold)

```html
<!DOCTYPE html>
<html lang="en">
<head>
<meta charset="utf-8">
<title>Wandering Rooms – Business Cards</title>
<link href="https://fonts.googleapis.com/css2?family=Montserrat:wght@300;400;600&display=swap" rel="stylesheet">
<style>
  :root {
    --stage: #1f1f1f;
    --card: #ffffff;
    --ink: #111111;
    --ink-soft: #333333;
    --silver: #b5b5b5;
    --white: #ffffff;
  }
  * { box-sizing: border-box; margin: 0; padding: 0; }
  html, body { width: 1200px; height: 900px; overflow: hidden; }
  body {
    background: var(--stage);
    font-family: "Montserrat", Arial, sans-serif;
    color: var(--ink);
    position: relative;
  }
  .card {
    position: absolute;
    left: 300px;
    width: 600px;
    height: 343px;
    background: var(--card);
    overflow: hidden;
  }
  .card--front { top: 80px; }
  .card--back { top: 470px; }
  .card-shapes {
    position: absolute;
    inset: 0;
    width: 600px;
    height: 343px;
  }
  .brand-name {
    position: absolute;
    font-weight: 400;
    font-size: 34px;
    letter-spacing: 0.04em;
    color: var(--ink);
    white-space: nowrap;
  }
  .card--front .brand-name {
    left: 0; right: 0; top: 130px;
    text-align: center;
  }
  .website {
    position: absolute;
    left: 0; right: 0; bottom: 48px;
    text-align: center;
    font-weight: 400;
    font-size: 12px;
    letter-spacing: 0.22em;
    color: var(--ink-soft);
  }
  .card--back .brand-name {
    left: 110px; top: 72px;
  }
  .person {
    position: absolute;
    right: 40px; top: 132px;
    padding-right: 12px;
    border-right: 2px solid var(--silver);
    text-align: right;
  }
  .person-name { font-weight: 600; font-size: 16px; color: var(--ink); }
  .person-role { font-weight: 400; font-size: 10px; color: var(--ink-soft); margin-top: 2px; }
  .contact-list {
    position: absolute;
    left: 54px; top: 216px;
    list-style: none;
  }
  .contact-list li {
    font-weight: 400;
    font-size: 11px;
    line-height: 30.5px;
    color: var(--ink);
    white-space: nowrap;
  }
</style>
</head>
<body>

<section class="card card--front" aria-label="Business card front">
  <svg class="card-shapes" viewBox="0 0 600 343" aria-hidden="true">
    <path d="M420,343 C434,343 432,327 448,327 L600,327 L600,343 Z" fill="var(--ink)"/>
  </svg>
  <div class="brand-name">Wandering Rooms</div>
  <div class="website">www.wanderingrooms-example.com</div>
</section>

<section class="card card--back" aria-label="Business card back">
  <svg class="card-shapes" viewBox="0 0 600 343" aria-hidden="true">
    <path d="M420,343 C434,343 432,327 448,327 L600,327 L600,343 Z" fill="var(--ink)"/>
    <path d="M0,206 L24,206 Q38,206 38,220 L38,330 Q38,343 25,343 L0,343 Z" fill="var(--ink)"/>
    <!-- phone -->
    <g transform="translate(19,232)" fill="none" stroke="var(--white)" stroke-width="1.4" stroke-linecap="round" stroke-linejoin="round">
      <path d="M-6,-2 Q0,-7 6,-2 L4,0 L2,-2 L-2,-2 L-4,0 Z"/>
      <rect x="-5" y="1" width="10" height="5" rx="1"/>
    </g>
    <!-- mail -->
    <g transform="translate(19,262)" fill="none" stroke="var(--white)" stroke-width="1.4" stroke-linejoin="round">
      <rect x="-6.5" y="-4.5" width="13" height="9"/>
      <path d="M-6.5,-4.5 L0,1 L6.5,-4.5"/>
    </g>
    <!-- globe -->
    <g transform="translate(19,292)" fill="none" stroke="var(--white)" stroke-width="1.2">
      <circle r="6.5"/>
      <ellipse rx="3" ry="6.5"/>
      <path d="M-6.5,0 H6.5 M-5.5,-3.5 H5.5 M-5.5,3.5 H5.5"/>
    </g>
    <!-- pin -->
    <g transform="translate(19,322)">
      <path d="M0,6 C-4,1 -6,-1 -6,-3 A6,6 0 0 1 6,-3 C6,-1 4,1 0,6 Z" fill="var(--white)"/>
      <circle cy="-3" r="2.2" fill="var(--ink)"/>
    </g>
  </svg>
  <div class="brand-name">Wandering Rooms</div>
  <div class="person">
    <div class="person-name">Marcus Hale</div>
    <div class="person-role">Managing Director</div>
  </div>
  <ul class="contact-list">
    <li>+971 2 518 2047</li>
    <li>mhale@wanderingrooms-example.com</li>
    <li>P.O. Box : 309186</li>
    <li>Block C&amp;D, Bldg. 47, Court 12, Abu Dhabi, United Arab Emirates</li>
  </ul>
</section>

</body>
</html>
```